Pepper & Palm Business Card FUN & EXCITING

Here is the Information for the Card:
Jaswinder Bains (Ravi)
E: RaviBains@postlark.com
C: (480) 555-0147
www.PepperPalmLV.com

We don't want traditional Indian cliche, We a playful bold and fun business card.

Files: https://files.cloudvessel.net/share/folders/7TqRmXpZ2vKa9LwBn4YcHd3JsEf6UoGi?usp=share_link

https://files.cloudvessel.net/share/folders/4MzXaQ8rTw2YbNcVk6PsLe5GhJdR3FoU?usp=share_link

Target Market(s)

Las Vegas Local Restaurant

Industry/Entity Type

Indian Restaurant

Contact Information for Business Card

Name, Email, Cell Phone, Company Logo

```html
<!DOCTYPE html>
<html lang="en">
<head>
<meta charset="UTF-8">
<title>Pepper &amp; Palm Business Card</title>
<link href="https://fonts.googleapis.com/css2?family=Montserrat:wght@400;600;700&display=swap" rel="stylesheet">
<style>
  :root {
    --backdrop: #2a2a2a;
    --card: #1d1d1d;
    --ink: #ffffff;
    --accent: #e8782c;
  }
  * { margin: 0; padding: 0; box-sizing: border-box; }
  html, body {
    width: 1200px;
    height: 1108px;
    overflow: hidden;
    background: var(--backdrop);
    font-family: "Montserrat", sans-serif;
  }
  .canvas { position: relative; width: 1200px; height: 1108px; }
  .card {
    position: absolute;
    left: 258px;
    width: 696px;
    background: var(--card);
    border-radius: 20px;
  }
  .card--front { top: 128px; height: 425px; }
  .card--back { top: 595px; height: 440px; }

  .brand-mark {
    position: absolute;
    left: 0; right: 0;
    top: 178px;
    text-align: center;
    color: var(--ink);
    font-weight: 700;
    font-size: 46px;
    letter-spacing: 0.5px;
  }

  .holder-name {
    position: absolute;
    left: 0; right: 0;
    top: 163px;
    text-align: center;
    color: var(--accent);
    font-weight: 600;
    font-size: 26px;
    padding-left: 12px;
  }
  .identity {
    position: absolute;
    left: 180px;
    top: 245px;
    display: flex;
    align-items: center;
  }
  .identity__brand {
    width: 116px;
    color: var(--ink);
    font-weight: 700;
    font-size: 22px;
    line-height: 1.1;
  }
  .identity__rule {
    width: 2px;
    height: 82px;
    background: var(--accent);
    margin: 0 10px 0 16px;
  }
  .contact-list { list-style: none; }
  .contact-list li {
    display: flex;
    align-items: center;
    height: 26px;
    color: var(--ink);
    font-size: 16px;
  }
  .contact-list svg { width: 14px; height: 14px; margin-right: 14px; fill: var(--accent); }
</style>
</head>
<body>
<div class="canvas">
  <section class="card card--front">
    <div class="brand-mark">Pepper &amp; Palm</div>
  </section>

  <section class="card card--back">
    <h1 class="holder-name">Jaswinder Bains (Ravi)</h1>
    <div class="identity">
      <div class="identity__brand">Pepper<br>&amp; Palm</div>
      <div class="identity__rule"></div>
      <ul class="contact-list">
        <li>
          <svg viewBox="0 0 16 16" aria-hidden="true"><path d="M1 5c0-2 3-3 7-3s7 1 7 3v1h-4V5H5v1H1z M3 8h10l1 6H2z"/></svg>
          (480) 555-0147
        </li>
        <li>
          <svg viewBox="0 0 16 16" aria-hidden="true"><path d="M1 3h14v2L8 9 1 5z M1 7l7 4 7-4v6H1z"/></svg>
          RaviBains@postlark.com
        </li>
        <li>
          <svg viewBox="0 0 16 16" aria-hidden="true"><path d="M8 1a7 7 0 1 0 0 14A7 7 0 0 0 8 1zm0 2c.8 1 1.4 2.6 1.5 4h-3C6.6 5.6 7.2 4 8 3zM3.1 7A5 5 0 0 1 5.4 3.7 9 9 0 0 0 4.5 7zm0 2h1.4a9 9 0 0 0 .9 3.3A5 5 0 0 1 3.1 9zm3.4 0h3c-.1 1.4-.7 3-1.5 4-.8-1-1.4-2.6-1.5-4zm5 0h1.4a5 5 0 0 1-2.3 3.3 9 9 0 0 0 .9-3.3zm0-2a9 9 0 0 0-.9-3.3A5 5 0 0 1 12.9 7z"/></svg>
          www.PepperPalmLV.com
        </li>
      </ul>
    </div>
  </section>
</div>
</body>
</html>
```